Tech business card design

We need an amazing business card design for our new business 'Pexla' a marketing tech startup based in Sydney, Australia. We provide an online marketplace for businesses to search and buy advertising media, connect with service providers and learn more about marketing. We wish to communicate 'cool tech', reliability and professionalism and design based around our logo.

Target Market(s)

Business Owners

Contact Information for Business Card

Name
Position
Email Address
Website
Phone Number

Font styles to use
Other font styles liked:
• Avenir & Avenir Next

Colors

Designer to choose colors to be used in the design.

```html
<!DOCTYPE html>
<html lang="en">
<head>
<meta charset="utf-8">
<title>Pexla Business Card</title>
<link rel="stylesheet" href="https://fonts.googleapis.com/css2?family=Nunito+Sans:wght@400;700;800&display=swap">
<style>
  :root {
    --stage: #e9e7e4;
    --card-dark: #17181b;
    --card-light: #ffffff;
    --logo-silver: #c9cacc;
    --web-grey: #b5b7ba;
    --navy: #1d1d4d;
    --title-grey: #7b7c80;
    --text-grey: #4a4b50;
    --rule: #55565a;
  }
  * { box-sizing: border-box; margin: 0; padding: 0; }
  html, body {
    width: 1200px;
    height: 864px;
    overflow: hidden;
    background: var(--stage);
    font-family: "Nunito Sans", "Avenir Next", Avenir, sans-serif;
  }
  .stage {
    width: 1200px;
    height: 864px;
    display: flex;
    align-items: center;
    justify-content: center;
    gap: 40px;
  }
  .card {
    position: relative;
    width: 540px;
    height: 309px;
    border-radius: 3px;
    box-shadow: 0 10px 28px rgba(0,0,0,0.18);
    overflow: hidden;
  }

  /* Back of card */
  .card--back { background: var(--card-dark); }
  .card--back .wordmark {
    position: absolute;
    left: 70px;
    top: 62px;
    font-size: 108px;
    font-weight: 800;
    letter-spacing: -3px;
    line-height: 1;
    color: var(--logo-silver);
  }
  .card--back .web {
    position: absolute;
    left: 72px;
    top: 206px;
    font-size: 14px;
    font-weight: 400;
    letter-spacing: 6px;
    color: var(--web-grey);
  }

  /* Front of card */
  .card--front { background: var(--card-light); }
  .card--front .wordmark {
    position: absolute;
    right: 34px;
    top: 54px;
    font-size: 72px;
    font-weight: 800;
    letter-spacing: -2px;
    line-height: 1;
    color: var(--navy);
  }
  .person {
    position: absolute;
    left: 30px;
    top: 132px;
  }
  .person .name {
    font-size: 17px;
    font-weight: 700;
    color: var(--navy);
    letter-spacing: 0.3px;
    line-height: 1.1;
  }
  .person .role {
    font-size: 14px;
    font-weight: 400;
    color: var(--title-grey);
    letter-spacing: 0.3px;
    line-height: 1.2;
  }
  .divider {
    position: absolute;
    left: 30px;
    right: 30px;
    top: 180px;
    height: 1px;
    background: var(--rule);
  }
  .contacts {
    position: absolute;
    left: 30px;
    top: 190px;
    list-style: none;
  }
  .contacts li {
    display: flex;
    align-items: center;
    gap: 9px;
    font-size: 13.5px;
    color: var(--text-grey);
    line-height: 21px;
  }
  .contacts svg { width: 11px; height: 11px; flex: none; }
</style>
</head>
<body>
<main class="stage">

  <section class="card card--back" aria-label="Card back">
    <div class="wordmark">pexla</div>
    <div class="web">www.pexlamedia.com.au</div>
  </section>

  <section class="card card--front" aria-label="Card front">
    <div class="wordmark">pexla</div>

    <div class="person">
      <p class="name">DANIEL REYES</p>
      <p class="role">FOUNDER, DIRECTOR</p>
    </div>

    <div class="divider"></div>

    <ul class="contacts">
      <li>
        <svg viewBox="0 0 12 12" aria-hidden="true">
          <rect x="2.5" y="0.5" width="7" height="11" rx="1.2" fill="none" stroke="#1d1d4d" stroke-width="1.2"/>
          <line x1="5" y1="9.5" x2="7" y2="9.5" stroke="#1d1d4d" stroke-width="1.2"/>
        </svg>
        +61 (0)400 555 018
      </li>
      <li>
        <svg viewBox="0 0 12 12" aria-hidden="true">
          <rect x="0.5" y="2" width="11" height="8" fill="#1d1d4d"/>
          <polyline points="0.8,2.4 6,6.6 11.2,2.4" fill="none" stroke="#ffffff" stroke-width="1"/>
        </svg>
        daniel@pexlamedia.com.au
      </li>
      <li>
        <svg viewBox="0 0 12 12" aria-hidden="true">
          <circle cx="6" cy="6" r="5.5" fill="#1d1d4d"/>
          <ellipse cx="6" cy="6" rx="2.2" ry="5" fill="none" stroke="#ffffff" stroke-width="0.8"/>
          <line x1="1" y1="6" x2="11" y2="6" stroke="#ffffff" stroke-width="0.8"/>
        </svg>
        www.pexlamedia.com.au
      </li>
    </ul>
  </section>

</main>
</body>
</html>
```